Rebrand stationary with recently completed logo design

Need new business cards, thank you cards, letterhead, envelopes and presentation folders. The designs will be sent to a separate production firm so I need the files to be print ready.

My contact info
Reko Haliburn

Office 604-318-5047
Fax 604-371-8054

Email reko@glazemark.ca
website www.glazemark.ca

315-14720 62nd Avenue,
Brenlow, MB, V2K 3R8

Target Market(s)

Homeowners, businesses and contractors

Industry/Entity Type

Business

Font styles to use
Sans Serif

Colors
34a7d7

Requirements
Must have
• Like to have one side of the business card a solid color with the logo in all white. The side with all the text to be a white background
• I find the current blue on the front of the card with the white logo too dark.
Should not have
• Gradient colors

```html
<!DOCTYPE html>
<html lang="en">
<head>
<meta charset="utf-8">
<title>Glazemark Business Card</title>
<link rel="stylesheet" href="https://fonts.googleapis.com/css2?family=Source+Sans+3:wght@400;600&display=swap">
<style>
  :root {
    --backdrop: #2b2b2b;
    --card-white: #f4f4f4;
    --brand-blue: #1592d2;
    --ink-dark: #4a525a;
    --ink-mid: #5c636a;
    --rule: #c9c9c9;
    --stripe-dark: #4a525a;
  }
  * { margin: 0; padding: 0; box-sizing: border-box; }
  html, body {
    width: 1200px; height: 960px; overflow: hidden;
    background: var(--backdrop);
    font-family: "Source Sans 3", "Myriad Pro", sans-serif;
  }
  .canvas { position: relative; width: 1200px; height: 960px; }

  .card { position: absolute; width: 600px; height: 342px; }
  .card-front { left: 302px; top: 129px; background: var(--card-white); }
  .card-back  { left: 299px; top: 488px; background: var(--brand-blue); }

  .front-stripe-line {
    position: absolute; left: 0; right: 0; top: 324px; height: 2px;
    background: var(--stripe-dark);
  }
  .front-stripe-band {
    position: absolute; left: 0; right: 0; bottom: 0; height: 14px;
    background: var(--brand-blue);
  }

  .wordmark {
    position: absolute; display: flex; align-items: center; gap: 10px;
    font-weight: 600; letter-spacing: 1px; line-height: 1;
    white-space: nowrap;
  }
  .wordmark .mark-square { display: block; flex: none; }
  .front-wordmark { left: 82px; top: 196px; color: var(--ink-dark); font-size: 34px; }
  .front-wordmark .mark-square { width: 22px; height: 22px; background: var(--ink-dark); }
  .back-wordmark { left: 126px; top: 148px; color: #ffffff; font-size: 48px; }
  .back-wordmark .mark-square { width: 32px; height: 32px; background: #ffffff; }

  .divider {
    position: absolute; left: 330px; top: 89px; width: 1px; height: 166px;
    background: var(--rule);
  }

  .contact { position: absolute; left: 359px; top: 93px; color: var(--ink-mid); white-space: nowrap; }
  .contact-name {
    font-size: 20px; font-weight: 600; color: var(--ink-dark);
    letter-spacing: 0.3px; line-height: 24px;
  }
  .contact-name .first { color: var(--brand-blue); }
  .contact-address { margin-top: 8px; font-size: 13.5px; line-height: 18px; }
  .contact-lines { margin-top: 8px; list-style: none; }
  .contact-lines li {
    display: flex; align-items: center; gap: 8px;
    font-size: 13.5px; line-height: 19.3px;
  }
  .contact-lines svg { width: 14px; height: 14px; fill: var(--brand-blue); flex: none; }
</style>
</head>
<body>
<div class="canvas">

  <section class="card card-front" aria-label="Business card front">
    <div class="wordmark front-wordmark">
      <span class="mark-square"></span><span class="wordmark-name">GLAZEMARK</span>
    </div>

    <div class="divider"></div>

    <div class="contact">
      <p class="contact-name"><span class="first">REKO</span> HALIBURN</p>
      <p class="contact-address">315-14720 62nd Avenue<br>Brenlow, MB, V2K 3R8</p>
      <ul class="contact-lines">
        <li>
          <svg viewBox="0 0 16 16" aria-hidden="true"><path d="M3.2 1.5l2.3-.5 1.6 3.4-1.5 1.2a8.6 8.6 0 0 0 4.8 4.8l1.2-1.5 3.4 1.6-.5 2.3c-.2.7-.8 1.2-1.5 1.2C7.4 14 2 8.6 2 3c0-.7.5-1.3 1.2-1.5z"/></svg>
          604-318-5047
        </li>
        <li>
          <svg viewBox="0 0 16 16" aria-hidden="true"><rect x="4" y="1" width="8" height="4"/><rect x="1" y="6" width="14" height="6" rx="1"/><rect x="4" y="10" width="8" height="5" fill="#fff"/><rect x="5" y="11" width="6" height="3"/></svg>
          604-371-8054
        </li>
        <li>
          <svg viewBox="0 0 16 16" aria-hidden="true"><path d="M1 4h14v9H1z"/><path d="M1.5 4.5L8 9.5l6.5-5" fill="none" stroke="#fff" stroke-width="1.3"/></svg>
          reko@glazemark.ca
        </li>
        <li>
          <svg viewBox="0 0 16 16" aria-hidden="true"><circle cx="8" cy="8" r="7"/><path d="M4 4.5c1.5.3 2.5 1.5 2 3s1.5 1.5 1.5 3-1 2-1 3M10 2.5c-.5 1.5.5 2.5 2 2.5s1.8 1 1.5 2.5" fill="none" stroke="#fff" stroke-width="1.2"/></svg>
          www.glazemark.ca
        </li>
      </ul>
    </div>

    <div class="front-stripe-line"></div>
    <div class="front-stripe-band"></div>
  </section>

  <section class="card card-back" aria-label="Business card back">
    <div class="wordmark back-wordmark">
      <span class="mark-square"></span><span class="wordmark-name">GLAZEMARK</span>
    </div>
  </section>

</div>
</body>
</html>
```